Private Investment Firm Needs PowerPoint Presentation Template

Design PowerPoint template, take Pinebrook-submitted rough presentation draft, and drop it into new template. See attached Project Brief file for more detail.
Updates

Some decent designs have been submitted but they seem to lack the understanding of our target markets. I am hopeful that more time and feedback will result in better results.

Target Market(s)

Private company owners and intermediaries.

Font styles to use
Serif

Colors
3176b5

Requirements
Must have
• See attached Project Brief.
Nice to have
Should not have
• No B2C fluff--this is a B2B project.

```html
<!DOCTYPE html>
<html lang="en">
<head>
<meta charset="utf-8">
<title>Pinebrook Capital – Introduction</title>
<link rel="stylesheet" href="https://fonts.googleapis.com/css2?family=Montserrat:wght@700&family=Questrial&display=swap">
<style>
  :root {
    --brand-blue: #1573c2;
    --band-blue: #1a7acb;
    --band-blue-light: #2a8ddc;
    --wedge-grey: #6e6f73;
    --text-grey: #3c3c3c;
    --page: #ffffff;
  }
  html, body { margin: 0; padding: 0; overflow: hidden; background: var(--page); }
  .slide {
    position: relative;
    width: 1200px; height: 770px;
    overflow: hidden;
    background: var(--page);
    font-family: "Questrial", sans-serif;
    color: var(--text-grey);
  }
  .slide__frame { position: absolute; inset: 0; }
  .slide__title {
    position: absolute; left: 0; width: 1226px; top: 94px; margin: 0;
    text-align: center;
    font-family: "Montserrat", sans-serif; font-weight: 700;
    font-size: 44px; letter-spacing: 1px;
    color: var(--brand-blue);
  }
  .slide__title-rule {
    position: absolute; left: 586px; top: 141px;
    width: 60px; height: 6px; border-radius: 3px;
    background: var(--brand-blue);
  }
  .point {
    position: absolute; left: 185px; width: 822px; margin: 0;
    font-size: 19.5px; line-height: 24.5px;
    text-align: justify; letter-spacing: 0.3px;
  }
  .point::before {
    content: ""; position: absolute; left: -30px; top: 7px;
    width: 6px; height: 6px; border-radius: 50%;
    background: var(--brand-blue);
  }
  .point--lead { text-align: left; }
  .subpoint {
    position: absolute; left: 232px; margin: 0;
    font-size: 19.5px; line-height: 24.5px; letter-spacing: 0.3px;
  }
  .subpoint::before {
    content: "\2713"; position: absolute; left: -20px; top: 0;
    font-size: 15px; color: var(--brand-blue);
  }
  .brand {
    position: absolute; left: 0; width: 1226px; top: 622px;
    display: flex; justify-content: center; align-items: center; gap: 10px;
  }
  .brand__dot { width: 22px; height: 22px; border-radius: 50%; background: var(--brand-blue); }
  .brand__name {
    font-family: "Questrial", sans-serif; font-size: 22px; letter-spacing: 2px;
    color: var(--text-grey);
  }
  .website {
    position: absolute; left: 0; width: 1226px; top: 683px; margin: 0;
    text-align: center; font-size: 20px; color: #1f1f1f;
  }
  .website strong { color: var(--brand-blue); font-weight: 400; }
  .page-number {
    position: absolute; left: 1101px; top: 666px;
    width: 52px; height: 52px; border: 3px solid #fff; border-radius: 50%;
    box-sizing: border-box;
    display: flex; align-items: center; justify-content: center;
    font-family: "Montserrat", sans-serif; font-weight: 700; font-size: 32px; color: #fff;
  }
</style>
</head>
<body>
<main class="slide">
  <svg class="slide__frame" width="1200" height="770" viewBox="0 0 1200 770" aria-hidden="true">
    <polygon points="0,0 120,0 0,568" fill="var(--wedge-grey)"/>
    <polygon points="1044,0 1200,0 1200,770 1042,770 1148,379" fill="var(--band-blue)"/>
    <polygon points="1200,200 1148,379 1042,770 1200,770" fill="var(--band-blue-light)"/>
  </svg>

  <h1 class="slide__title">INTRODUCTION</h1>
  <div class="slide__title-rule"></div>

  <p class="point point--lead" style="top:184px">Private company owners have traditionally considered two capital raising options</p>
  <p class="subpoint" style="top:220px">Borrow from a local bank, or</p>
  <p class="subpoint" style="top:253px">Sell most or all of the company to a change- of-control investor (aka Buyout firm)</p>

  <p class="point" style="top:308px">An alternative most have not considered is the raising of Non-Control Capital, orcapital that is invested into the business yet allows those same owners to retaincontrolling interest in their company</p>

  <p class="point" style="top:415px">Non-Control Capital is not appropriate for every private company owner but neither is a Change-of-Control sale</p>

  <p class="point" style="top:498px">The key is to determine what the business and owners require, and then partner withan investor best aligned with those needs so that long-term company growth, and personal goals, can both be achieved</p>

  <div class="brand">
    <span class="brand__dot"></span>
    <span class="brand__name">PINEBROOK CAPITAL</span>
  </div>
  <p class="website">www.<strong>pinebrookcapital</strong>.com</p>

  <div class="page-number">1</div>
</main>
</body>
</html>
```